Automotive component supplier needs a business card design

We need a business card design for our company called Velran Global Components Ltd based in the UK. We are a supplier of interior and exterior components to premium car manufacturers such as Corvel Ashby, Hadley Fenn, Marquist and Tavarelli. We would like to see a modern business card design that uses the colour blue.

Target Market(s)

Premium automotive car manufacturers.

Industry/Entity Type

Automotive

Contact Information for Business Card

Company Name : Velran Global Components Limited
Address: 17 Marlow Yard, Upper Heath, Warwick, CV31 8QL, United Kingdom
Web Address : www.velrancomponents-example.co.uk

Font styles to use
Other font styles liked:
• Helvetica

Colors
3176b5
0255a3
85acd3
cfdeed
cee9f5
85cae6
34a6d7
0692cd
9bcb3c

Requirements
Must have
• Clear company logo and a mixture of blue colours.
Nice to have
• A high quality modern image.
Should not have
• Multiple colours.

```html
<!DOCTYPE html>
<html lang="en">
<head>
<meta charset="utf-8">
<title>Velran Global Components – Business Card</title>
<link href="https://fonts.googleapis.com/css2?family=Arimo:wght@400;700&display=swap" rel="stylesheet">
<style>
  :root {
    --bg: #2b2b2d;
    --card-blue: #1b95d4;
    --pattern-light: #2aa2dd;
    --pattern-dark: #1688c6;
    --ink-black: #050505;
    --accent-green: #9bcb3c;
    --text-white: #ffffff;
  }
  html, body {
    margin: 0;
    width: 1200px;
    height: 900px;
    overflow: hidden;
    background: var(--bg);
    font-family: "Arimo", Helvetica, Arial, sans-serif;
  }
  .stage {
    position: relative;
    width: 1200px;
    height: 900px;
  }
  .card {
    position: absolute;
    width: 660px;
    height: 377px;
    overflow: hidden;
    box-shadow: 0 12px 30px rgba(0,0,0,0.45);
  }
  /* Back of card */
  .card-back {
    left: 150px;
    top: 48px;
    background: var(--card-blue);
  }
  .card-back .pattern-field {
    position: absolute;
    inset: 0;
    background: linear-gradient(135deg, var(--pattern-light), var(--pattern-dark));
  }
  .brand-lockup {
    position: absolute;
    right: 40px;
    bottom: 46px;
    text-align: left;
    color: var(--text-white);
  }
  .brand-lockup .brand-row {
    display: flex;
    align-items: center;
    gap: 10px;
  }
  .brand-lockup .brand-square {
    width: 14px;
    height: 14px;
    background: var(--accent-green);
    border-radius: 2px;
  }
  .brand-lockup .brand-name {
    font-weight: 700;
    font-size: 50px;
    letter-spacing: 1px;
    line-height: 1;
  }
  .brand-lockup .brand-sub {
    font-size: 13px;
    letter-spacing: 1.6px;
    margin-top: 4px;
    padding-left: 24px;
  }
  /* Front of card */
  .card-front {
    left: 390px;
    top: 475px;
    background: var(--card-blue);
  }
  .card-front .panel-shape {
    position: absolute;
    inset: 0;
  }
  .front-brand {
    position: absolute;
    left: 48px;
    top: 170px;
    font-weight: 700;
    font-size: 40px;
    letter-spacing: 1px;
    color: var(--card-blue);
  }
  .contact-block {
    position: absolute;
    right: 40px;
    top: 44px;
    text-align: right;
    color: var(--text-white);
  }
  .person-name {
    font-weight: 700;
    font-size: 22px;
    letter-spacing: 1.5px;
    margin: 0;
  }
  .person-title {
    color: var(--accent-green);
    font-size: 15px;
    margin: 2px 0 14px;
  }
  .contact-line {
    font-size: 15px;
    line-height: 21px;
    margin: 0;
    display: flex;
    justify-content: flex-end;
    align-items: center;
    gap: 8px;
  }
  .contact-line .icon {
    width: 12px;
    height: 12px;
    flex: none;
  }
  .contact-line .icon-spacer {
    width: 12px;
    flex: none;
  }
  .address { margin-bottom: 8px; }
</style>
</head>
<body>
<main class="stage">

  <section class="card card-back" aria-label="Business card back">
    <div class="pattern-field" role="img" aria-label="Repeating brand motif pattern in blue tones"></div>
    <div class="brand-lockup">
      <div class="brand-row">
        <span class="brand-square"></span>
        <span class="brand-name">VELRAN</span>
      </div>
      <div class="brand-sub">GLOBAL COMPONENTS</div>
    </div>
  </section>

  <section class="card card-front" aria-label="Business card front">
    <svg class="panel-shape" viewBox="0 0 660 377" preserveAspectRatio="none" aria-hidden="true">
      <path d="M0 0 H250 C325 110 330 250 255 377 H0 Z" fill="var(--accent-green)"/>
      <path d="M0 0 H236 C308 110 312 250 240 377 H0 Z" fill="var(--ink-black)"/>
    </svg>
    <div class="front-brand">VELRAN</div>

    <div class="contact-block">
      <p class="person-name">DORIAN PELLEY</p>
      <p class="person-title">Director</p>
      <div class="address">
        <p class="contact-line">17 Marlow Yard, Upper Heath<span class="icon-spacer"></span></p>
        <p class="contact-line">Warwick, CV31 8QL, UK<span class="icon-spacer"></span></p>
      </div>
      <p class="contact-line">780 555-0142
        <svg class="icon" viewBox="0 0 12 12"><path d="M2 1 L4 1 L5 4 L3.5 5 Q5 7.5 7 8.5 L8 7 L11 8 L11 10 Q10 11 8.5 11 Q2 9 1 2.5 Q1 1 2 1Z" fill="var(--accent-green)"/></svg>
      </p>
      <p class="contact-line">780 555-0187
        <svg class="icon" viewBox="0 0 12 12"><rect x="3" y="0.5" width="6" height="11" rx="1" fill="none" stroke="var(--accent-green)" stroke-width="1.2"/><circle cx="6" cy="9.5" r="0.7" fill="var(--accent-green)"/></svg>
      </p>
      <p class="contact-line">velrancomponents@example.com
        <svg class="icon" viewBox="0 0 12 12"><rect x="0.5" y="2.5" width="11" height="7.5" fill="var(--accent-green)"/><path d="M0.5 2.5 L6 7 L11.5 2.5" fill="none" stroke="var(--card-blue)" stroke-width="1"/></svg>
      </p>
      <p class="contact-line">www.velrancomponents-example.co.uk
        <svg class="icon" viewBox="0 0 12 12"><circle cx="6" cy="6" r="5" fill="none" stroke="var(--accent-green)" stroke-width="1.2"/><ellipse cx="6" cy="6" rx="2" ry="5" fill="none" stroke="var(--accent-green)"/><line x1="1" y1="6" x2="11" y2="6" stroke="var(--accent-green)"/></svg>
      </p>
    </div>
  </section>

</main>
</body>
</html>
```